Stonebrace Business Card Design

The Stonebrace Co is an aggregate (crushing) equipment dealer serving Western Canadian provinces. Stonebrace is a distributor of aggregate equipment for different manufacturers.

We are looking to change and update the existing business card which has been used since the existence of the company. A copy of existing card has been attached for reference. The Stonebrace Co logo we want to remain the same and we want the green color to remain the same.

We are wanting something new with a different look. A refreshing card to show a new modern and updated look. No longer wanting to have the manufacturers on the back of the card but something more like our logo on the back of the card with a statement like "Crushing Solutions"

ideas could be:
- card can be different colors on front and back
- front or reverse of the card could possibly be the green color with the logo in black

Target Market(s)

Owners of Aggregate/Crushing companies

Contact Information for Business Card

see above

Requirements
Must have
• - logo to remain same along with same font within logo
• - green color to remain same
Nice to have
• as noted above under project description
Should not have

```html
<!DOCTYPE html>
<html lang="en">
<head>
<meta charset="utf-8">
<title>The Stonebrace Co – Business Card</title>
<link rel="stylesheet" href="https://fonts.googleapis.com/css2?family=Roboto:wght@400;500;700&family=Roboto+Condensed:wght@700&display=swap">
<style>
  :root {
    --stage: #e6e2dc;
    --brand-green: #878a0b;
    --brand-green-dark: #6f7209;
    --ink: #231f20;
    --paper: #f7f7f5;
    --text-grey: #4a4a4a;
    --rule: #8c8c8c;
  }
  * { margin: 0; padding: 0; box-sizing: border-box; }
  html, body { width: 1200px; height: 960px; overflow: hidden; }
  body {
    background: var(--stage);
    font-family: "Roboto", Arial, sans-serif;
    position: relative;
  }
  .card {
    position: absolute;
    left: 320px;
    width: 600px;
    height: 342px;
    border-radius: 20px;
    overflow: hidden;
  }
  /* Front */
  .card-front {
    top: 108px;
    background: var(--brand-green);
    color: var(--ink);
    text-align: center;
  }
  .front-mark {
    position: absolute;
    left: 50%;
    top: 98px;
    width: 70px;
    height: 70px;
    margin-left: -35px;
    border-radius: 50%;
    background: var(--ink);
  }
  .front-name {
    position: absolute;
    left: 0; right: 0;
    top: 218px;
    font-weight: 700;
    font-size: 23px;
    letter-spacing: 0.2px;
  }
  .front-tagline {
    position: absolute;
    left: 0; right: 0;
    top: 292px;
    font-weight: 500;
    font-size: 14px;
  }
  /* Back */
  .card-back {
    top: 493px;
    background: var(--paper);
  }
  .back-brand {
    position: absolute;
    right: 32px;
    top: 52px;
    display: flex;
    align-items: center;
    gap: 12px;
  }
  .back-brand-dot {
    width: 26px; height: 26px;
    border-radius: 50%;
    background: var(--brand-green);
  }
  .back-brand-name {
    font-weight: 700;
    font-size: 19px;
    color: var(--ink);
  }
  .person-name {
    position: absolute;
    left: 27px;
    top: 160px;
    font-family: "Roboto Condensed", "Arial Narrow", sans-serif;
    font-weight: 700;
    font-size: 21px;
    color: var(--brand-green);
  }
  .person-title {
    position: absolute;
    left: 27px;
    top: 186px;
    font-weight: 500;
    font-size: 14px;
    color: var(--ink);
  }
  .divider {
    position: absolute;
    left: 27px;
    top: 211px;
    width: 539px;
    height: 1px;
    background: var(--rule);
  }
  .contact-list {
    position: absolute;
    left: 28px;
    top: 225px;
    list-style: none;
    font-size: 14px;
    color: var(--text-grey);
  }
  .contact-list li {
    display: flex;
    align-items: center;
    height: 19px;
    gap: 8px;
  }
  .contact-list svg { width: 14px; height: 14px; fill: var(--brand-green); }
  .address {
    position: absolute;
    right: 30px;
    top: 265px;
    text-align: right;
    font-size: 14px;
    line-height: 18px;
    color: var(--text-grey);
  }
  .footer-band {
    position: absolute;
    left: 0; bottom: 0;
    width: 600px; height: 30px;
  }
  .website {
    position: absolute;
    right: 25px;
    bottom: 6px;
    font-size: 14px;
    letter-spacing: 2.4px;
    color: #ffffff;
  }
</style>
</head>
<body>

<section class="card card-front" aria-label="Card front">
  <span class="front-mark"></span>
  <h1 class="front-name">THE STONEBRACE CO.</h1>
  <p class="front-tagline">Crushing Solutions</p>
</section>

<section class="card card-back" aria-label="Card back">
  <div class="back-brand">
    <span class="back-brand-dot"></span>
    <span class="back-brand-name">THE STONEBRACE CO.</span>
  </div>

  <h2 class="person-name">DALE MARSDEN</h2>
  <p class="person-title">CEO/FOUNDER</p>
  <div class="divider"></div>

  <ul class="contact-list">
    <li><svg viewBox="0 0 16 16"><path d="M3.5 1l2.5 3-1.5 1.6c.8 2 2.4 3.6 4.4 4.4L10.5 8.5l3 2.5-1.5 3C6.5 14 2 9.5 1.9 4z"/></svg>780.555.0142</li>
    <li><svg viewBox="0 0 16 16"><path d="M4 0h8v16H4zM5.5 2v10h5V2zM7 13.2h2v1.3H7z" fill-rule="evenodd"/></svg>780.555.0187</li>
    <li><svg viewBox="0 0 16 16"><path d="M4 1h8v4H4zM1 6h14v6h-3v3H4v-3H1zM5 10v4h6v-4z" fill-rule="evenodd"/></svg>780.555.0163</li>
    <li><svg viewBox="0 0 16 16"><path d="M1 4h14v9H1zM2 5l6 4.5L14 5z" fill-rule="evenodd"/></svg>dale@stonebr.com</li>
  </ul>

  <p class="address">2219- 48B Avenue<br>Nisku, Alberta T9E 1X2</p>

  <svg class="footer-band" viewBox="0 0 600 30" preserveAspectRatio="none" aria-hidden="true">
    <rect x="0" y="10" width="380" height="11" fill="var(--ink)"/>
    <path d="M0 21h340c18 0 22-13 40-13H600v22H0z" fill="var(--paper)"/>
    <path d="M360 30c10 0 12-16 30-16H600V30z" fill="var(--brand-green)" transform="translate(0,-14) scale(1,1.45)"/>
  </svg>
  <span class="website">www.stonebrace.ca</span>
</section>

</body>
</html>
```